Broschüren-Design für Bauunternehmen
Zielgruppe
Wir bauen Neubauten in Massiv Bauweise, als Bauträger und Generalunternehmer in Raum Baden-Baden und Umgebung. Zielgruppe sind alle Altersgruppen, jedoch möchten wir gerade junge Familien mit Kindern unterstützen ihr e induvidueles Traumhaus mit Festpreis Garantien kostenbewusst zu ermöglichen.
Aufgabenstellung
Es sollte eine Image Broschüre Größe A4 in 12 Seiten ergeben. Unter Berücksichtigung dass es ein Imagespiegelung unseres website
design sollte.
Die Textinhalte sollten aus der Webseite übernommen werden und dürfen auch passend gekürzt werden.
Logo, Bilder welches in der Webseite ersichtlich sind sollten verwendet werden. Es können jedoch stock-bilder, Vektor Dateien bei bedarf verwendet werden. Diese werden dann dazu gekauft.
Inhalt:
Seite 1 - Startbild, Logo und Überschrift „Fest-gefügt - Rundum aus einem Guss - Vorlind Bauunternehmung aus Baden-Baden!'
Seite 2 - Philosophie, Bild Geschäftsführer; (Text siehe Startseite unter „Wir sind als Bauträger..........Wir beraten Sie gerne!')
Seite 3 - Über Uns, Bild Beratung (Text siehe über uns)
Seite 4 / 5 - Rundum Sicherheitspaket, Bilder Hand und Familie und Garantie Siegel (Text Leistungen/Sicherheitspaket)
Seite 6/7 - Bauberatung Bilder siehe Webseite
Seite 8 - Massivbau und Monolithische Bauweise ( Text Bauwissen/Massivbau und Bauwissen/Monolithische Bauweise) Wichtig Text passend kürzen.....
Seite 9 - Wohnraumlüftung - Bild siehe Webseite (Text Bauwissen/Raumklima)
Seite 10/11 - Finanzierung und BRT-Standards (Text Bauwissen)
Seite 12 - Kontakt und Adresse
Wie gesagt Designfarbe wie Webseite und logo. Längere Texte können zweispaltig geschrieben werden. Texte können gekürzt werden.
Bild Herkünfte siehe Impressum. können bei stock als Entwurf heruntergeladen werden. bei Finnisch werden sie nachgereicht.

```html
<!DOCTYPE html>
<html lang="de">
<head>
<meta charset="utf-8">
<title>Vorlind Bauunternehmung – Broschüre</title>
<link href="https://fonts.googleapis.com/css2?family=Open+Sans:wght@300;400;600;700&display=swap" rel="stylesheet">
<style>
:root{
  --board:#3a3c37;
  --panel:#3a3c37;
  --paper:#ffffff;
  --yellow:#e8b01a;
  --yellow-text:#e6ae1f;
  --stage:#e4e4e7;
  --ink:#2d2d2a;
  --ink-dark:#3b3422;
}
*{margin:0;padding:0;box-sizing:border-box}
html,body{width:1200px;height:2400px;overflow:hidden}
body{position:relative;font-family:"Open Sans",Arial,sans-serif;background:var(--stage);color:var(--ink)}
.board{position:absolute;left:0;top:0;width:1200px;height:1761px;background:var(--board)}
.stage{position:absolute;left:0;top:1761px;width:1200px;height:639px;background:var(--stage)}
.abs{position:absolute}
.section-label{position:absolute;color:#fff;font-weight:400;font-size:29px;white-space:nowrap;transform:rotate(-90deg);transform-origin:left top}

/* Spread: Bauwissen */
.spread{position:absolute;background:var(--paper)}
.spread-knowledge{left:191px;top:67px;width:757px;height:535px}
.knowledge-panel{position:absolute;left:18px;top:19px;width:721px;height:498px;background:var(--panel)}
.knowledge-title{position:absolute;left:65px;top:34px;color:var(--yellow-text);font-size:16px;font-weight:400}
.bulb{position:absolute;left:16px;top:20px}
.photo-strip{position:absolute;left:0;top:104px}
.col{position:absolute;top:250px;color:#e9e9e4;font-size:5.6px;line-height:7.6px}
.col h3{color:var(--yellow-text);font-weight:400;font-size:10.5px;line-height:13px;margin-bottom:7px}
.col p{margin-bottom:7.6px}
.col b{font-weight:700}
.col ul{list-style:none}
.col li::before{content:"✔ ";font-size:5px}

/* Spread: Finanzierung */
.spread-finance{left:191px;top:621px;width:757px;height:535px}
.finance-panel{position:absolute;left:18px;top:17px;width:721px;height:500px;background:var(--yellow)}
.finance-photo{position:absolute;left:0;top:17px}
.finance-heading{position:absolute;left:49px;top:362px;color:#fff;font-weight:300;font-size:17px;line-height:21px}
.finance-intro{position:absolute;left:49px;top:413px;width:265px;color:#fff;font-size:7.8px;line-height:10.4px}
.offer{position:absolute;left:430px;width:255px;color:#fff}
.offer h4{font-weight:300;font-size:10.5px;line-height:12.5px;margin-bottom:5px}
.offer p{font-size:5.3px;line-height:7.4px;color:#fff}
.offer-icon{position:absolute;left:-58px;top:-5px}

/* Pages */
.page{position:absolute;background:var(--paper)}
.contact-page{left:191px;top:1174px;width:378px;height:535px}
.contact-photo{position:absolute;left:0;top:128px}
.contact-lead{position:absolute;left:49px;top:405px;color:var(--yellow-text);font-weight:700;font-size:7.8px;line-height:10.4px}
.contact-lines{position:absolute;left:49px;top:451px;color:var(--ink);font-weight:700;font-size:7.8px;line-height:10px}
.contact-lines .gap{height:9px}
.contact-web{position:absolute;right:34px;top:489px;color:var(--yellow-text);font-weight:700;font-size:7.8px}

.back-page{left:225px;top:1836px;width:331px;height:478px}
.back-page .contact-photo{top:114px}
.back-page .contact-lead{left:44px;top:362px;font-size:7px;line-height:9.3px}
.back-page .contact-lines{left:44px;top:403px;font-size:7px;line-height:9px}
.back-page .contact-lines .gap{height:8px}
.back-page .contact-web{right:30px;top:437px;font-size:7px}

.cover-page{left:595px;top:1836px;width:332px;height:478px}
.cover-brand{position:absolute;left:0;top:54px;width:100%;text-align:center;color:var(--ink);font-weight:600;font-size:14px}
.cover-photo{position:absolute;left:0;top:114px}
.cover-claim{position:absolute;left:0;top:408px;width:100%;text-align:center;color:var(--yellow-text);font-weight:600;font-size:10.5px;line-height:14px}
</style>
</head>
<body>

<div class="board">
  <div class="section-label" style="left:143px;top:205px">Bauwissen</div>
  <div class="section-label" style="left:143px;top:1040px">Finanzierung und BRT-Standards</div>
  <div class="section-label" style="left:143px;top:1270px">Kontakt</div>

  <!-- Bauwissen spread -->
  <section class="spread spread-knowledge">
    <div class="knowledge-panel">
      <svg class="bulb" width="40" height="68" viewBox="0 0 40 68" aria-hidden="true">
        <path d="M4 10 a14 14 0 1 1 14 28 v10 h-12" fill="none" stroke="#fff" stroke-width="5"/>
        <rect x="0" y="52" width="18" height="4" fill="#fff"/>
        <rect x="0" y="59" width="18" height="4" fill="#fff"/>
        <line x1="30" y1="4" x2="34" y2="0" stroke="#fff" stroke-width="3"/>
        <line x1="35" y1="16" x2="40" y2="15" stroke="#fff" stroke-width="3"/>
        <line x1="33" y1="29" x2="38" y2="32" stroke="#fff" stroke-width="3"/>
      </svg>
      <div class="knowledge-title">Bauwissen</div>
    </div>
    <svg class="photo-strip" width="757" height="121" viewBox="0 0 757 121">
      <g role="img" aria-label="Weiße Porenbetonsteine, gestapelt">
        <polygon points="0,0 200,0 155,121 0,121" fill="#d9dce2"/>
      </g>
      <g role="img" aria-label="Hellgrünes Reihenhaus mit Balkonen und Garten">
        <polygon points="200,0 420,0 465,121 155,121" fill="#b9c98a"/>
      </g>
      <g role="img" aria-label="Hand bedient ein Tablet mit Smart-Home-Raumklimasteuerung">
        <polygon points="420,0 757,0 757,121 465,121" fill="#6f7f96"/>
      </g>
    </svg>

    <div class="col" style="left:61px;width:118px">
      <h3>Massivbau</h3>
      <p>Ein eigenes Heim steht auf der Wunschliste vieler Bundesbürger ganz oben, bietet diese Wohnform doch ein Höchstmaß an Komfort, Individualität und Sicherheit, auch ist die Perspektive verlockend, künftig keine Miete bezahlen zu müssen. Eigenheime können in Fertig- oder Massivbauweise errichtet werden, wobei die massive Bauform über einige Vorzüge verfügt, welche in diesem Artikel dargestellt werden.</p>
      <p><b>Vorteile:</b><br>Massivhäuser zeichnen sich durch eine Reihe von Vorzügen aus, die einen gegenüber Fertighäusern höheren Kaufpreis, bzw. höhere Baukosten vollends rechtfertigen. Nachstehend eine Übersicht der wichtigsten Pluspunkte massiver Bauart.</p>
      <ul><li>Energetische Effizienz</li><li>Wertbeständigkeit</li><li>Brand- und Schallschutz</li></ul>
    </div>
    <div class="col" style="left:201px;width:124px">
      <h3>Monolithische Bauweise</h3>
      <p>Die sogenannte monolithische Bauweise erfreut sich bei Bauherren einer wachsenden Beliebtheit. Dies ist nicht weiter verwunderlich, zumal diese Lösung eine Vielzahl an Vorteilen vorzuweisen hat. Zum Einsatz kommt hierbei der sogenannte Porenbeton, ein Baustoff, der höchste Wohnqualität verspricht und sämtliche Vorgaben nach der Energieeinsparverordnung (EnEV) sogar übertrifft.</p>
      <p><b>Vorteile:</b><br>Nicht nur die hervorragenden Wärmedämmeigenschaften sprechen für die Bauweise, monolithische Bauweise. Das bauen Stein auf Stein mit Porenbeton weist außerdem folgende Vorzüge auf:</p>
      <ul><li>Wirksamer Schallschutz</li><li>Wertbeständigkeit</li><li>Tragfähig und massiv</li><li>Umweltschonend</li><li>Wirtschaftlich</li><li>Brandschutz</li><li>Raumklima</li></ul>
    </div>
    <div class="col" style="left:433px;width:126px">
      <h3>Raumklima Lüftungskonzept</h3>
      <p>Die kontrollierte Gebäudelüftung mittels technischer Lüftungsanlage entspricht dem aktuellen Stand des Wohnbaus und ist heute fester Bestandteil jeder energetischen Wohnraumplanung. Ausgehend von unterschiedlichen Lüftungskonzepten existieren für derartige Anlagen diverse Fördermöglichkeiten. Lesen Sie mehr!</p>
      <p>Regelmäßiges und richtiges Lüften zählt zu den wichtigsten Aufgabenstellungen auf dem Weg zu einer angemessenen Wohnqualität. Der Lüftungsprozess beugt Feuchte und mit schädlicher Schimmelbildung einhergehender Raumluft vor, indem Frischluft zugeführt und verbrauchte Atemluft nach draußen abtransportiert wird. Wird in den Einbau einer automatischen Lüftungsanlage investiert, sorgt diese nicht nur für regelmäßigen Luftaustausch, sondern schützt durch moderne Filtertechnik auch vor Pollen und Bakterien, die bei derartigen Geräten üblicherweise eingesetzte Wärmerückgewinnungs-Technologie sorgt für eine hohe Energieeffizienz des Systems.</p>
    </div>
    <div class="col" style="left:577px;width:126px;top:270px">
      <p><b>✔ Dezentrale Lüftungsanlage</b><br>Dieses Lüftungssystem punktet mit vergleichsweise moderaten Anschaffungskosten und repräsentiert eine flexible Variante kontrollierten Luftaustausches einschließlich Wärmerückgewinnung. Weitere Vorteile bestehen in dem geringen Installationsaufwand, den relativ geringen Betriebs- und Wartungskosten der Anlage.</p>
      <p><b>✔ Zentrale Lüftungsanlage</b><br>Ein Belüftungskonzept für maximalen Wohnkomfort bei durch Wärmerückgewinnung bedingter hoher Energieeffizienz, welches auch zur Kühlung von Innenräumen eingesetzt werden kann. In der Zentraleinheit sorgt ein Wärmetauscher für eine effiziente Rückgewinnung von Wärme.</p>
      <p><b>✔ Fensterfalzlüftung</b><br>Das Prinzip dieses Lüftungssystems beruht auf der Aufrechterhaltung eines kontinuierlichen Luftstromes zwischen zwei parallelen Gebäudeseiten. Da keine elektrische Ventilation erforderlich ist, fallen keine Betriebskosten an.</p>
    </div>
  </section>

  <!-- Finanzierung spread -->
  <section class="spread spread-finance">
    <div class="finance-panel"></div>
    <svg class="finance-photo" width="378" height="295" viewBox="0 0 378 295">
      <g role="img" aria-label="Modellhaus mit rotem Giebel auf Bauplänen, Euro-Geldscheinen, Münzen und Schlüsseln">
        <polygon points="0,0 378,0 378,295 78,295 18,230 0,230" fill="#cfc6b8"/>
      </g>
    </svg>
    <h2 class="finance-heading">Baufinanzierung und<br>BRT-Standards</h2>
    <p class="finance-intro">Träumen auch Sie von einem eigenen Haus für Ihre Familie? Dann ist jetzt der richtige Zeitpunkt, um Ihre Träume Wirklichkeit werden zu lassen: Die aktuellen Niedrigzinsen sorgen für erschwingliche Konditionen bei der Baufinanzierung.</p>

    <div class="offer" style="top:58px">
      <svg class="offer-icon" width="56" height="56" viewBox="0 0 56 56" aria-hidden="true">
        <circle cx="28" cy="28" r="26.5" fill="none" stroke="#fff" stroke-width="1.6"/>
        <path d="M14 34 h6 l8 4 h8 l6-5" fill="none" stroke="#fff" stroke-width="1.6"/>
        <circle cx="26" cy="25" r="5" fill="none" stroke="#fff" stroke-width="1.6"/>
        <circle cx="34" cy="17" r="4" fill="none" stroke="#fff" stroke-width="1.6"/>
      </svg>
      <h4>Baufinanzierung für Ihr Eigenheim</h4>
      <p>Immobilienkredite mit zehn Jahren Laufzeit bekommen Sie momentan mit Zinssätzen von deutlich unter 1,5 %. Die niedrigen Zinssätze bedeuten für Sie, dass Sie Ihre Immobilie derzeit besonders günstig finanzieren können. Ihr Vorlind Bauunternehmen empfiehlt: Nutzen Sie auch die günstigen staatlichen Förderangebote zur Finanzierung Ihres Eigenheims! Die staatliche Förderbank BRT bietet Ihnen und Ihrer Familie verschiedene Kredite und Zuschüsse, mit denen Sie sich die Baufinanzierung zusätzlich erleichtern können. Die meisten Förderangebote der BRT sind flexibel untereinander kombinierbar.</p>
    </div>
    <div class="offer" style="top:172px">
      <svg class="offer-icon" width="56" height="56" viewBox="0 0 56 56" aria-hidden="true">
        <circle cx="28" cy="28" r="26.5" fill="none" stroke="#fff" stroke-width="1.6"/>
        <path d="M14 29 L28 16 L42 29 M18 26 V40 H38 V26 M25 40 V32 H31 V40" fill="none" stroke="#fff" stroke-width="1.6"/>
      </svg>
      <h4>BRT-Wohneigentumsprogramm<br>(BRT-Programm 124)</h4>
      <p>Wenn Sie eine Immobilie für sich und Ihre Familie bauen möchten, kommt das BRT-Wohneigentumsprogramm für Sie infrage. Es handelt sich um einen staatlich geförderten Kredit mit günstigen Konditionen: Wer eine Immobilie zur eigenen Nutzung baut oder kauft, kann hierfür einen Kredit von bis zu 50.000 Euro erhalten. Dank der aktuellen Zinslage bekommen Sie die Förderung ab einem effektiven Jahreszins von 1,0 %. Das BRT-Wohneigentumsprogramm können Sie übrigens auch wahrnehmen, wenn Sie die Immobilie einem Familienmitglied überlassen möchten. Sie können die Förderung also beispielsweise auch verwenden, um Ihren Eltern eine altersgerecht gestaltete Immobilie zu bauen.</p>
    </div>
    <div class="offer" style="top:297px">
      <svg class="offer-icon" width="56" height="56" viewBox="0 0 56 56" aria-hidden="true">
        <circle cx="28" cy="28" r="26.5" fill="none" stroke="#fff" stroke-width="1.6"/>
        <path d="M28 42 V28 M28 30 C20 30 15 24 15 18 C23 18 28 23 28 30 M28 30 C36 30 41 24 41 18 C33 18 28 23 28 30" fill="none" stroke="#fff" stroke-width="1.6"/>
      </svg>
      <h4>Energieeffizient Bauen<br>(BRT-Programm 153)</h4>
      <p>Sie möchten einen energieeffizienten Massivbau nach den neuesten Standards bauen? Die BRT fördert Ihr Bauvorhaben mit einem Kredit von bis zu 100.000 Euro. Derzeit bekommen Sie den Kredit bereits ab 1,26 % effektivem Jahreszins. Die Förderung gilt für neu gekaufte oder gebaute Wohnimmobilien, die den technischen Standards für die BRT-Effizienzhäuser 55, 40 oder 40 Plus entsprechen – gerne beraten wir von Vorlind Sie zu den förderfähigen Standards und helfen Ihnen dabei, das optimale BRT-Effizienzhaus für Ihre Familie zu wählen.</p>
    </div>
    <div class="offer" style="top:406px">
      <svg class="offer-icon" width="56" height="56" viewBox="0 0 56 56" aria-hidden="true">
        <circle cx="28" cy="28" r="26.5" fill="none" stroke="#fff" stroke-width="1.6"/>
        <circle cx="33" cy="22" r="7" fill="none" stroke="#fff" stroke-width="1.6"/>
        <ellipse cx="24" cy="32" rx="9" ry="5" transform="rotate(-45 24 32)" fill="none" stroke="#fff" stroke-width="1.6"/>
        <circle cx="19" cy="37" r="3.5" fill="none" stroke="#fff" stroke-width="1.6"/>
      </svg>
      <h4>Baukindergeld: Zuschuss für Familien<br>(BRT-Programm 424)</h4>
      <p>Sie haben Kinder und möchten sich und Ihrer Familie den Traum vom Eigenheim erfüllen? Dann haben Sie nach dem Einzug möglicherweise Anspruch auf einen staatlichen Zuschuss. Das Baukindergeld richtet sich an Familien und Alleinerziehende mit mindestens einem Kind, für das Kindergeld bezogen wird. Pro Kind erhalten Sie zehn Jahre lang jährlich einen Zuschuss von 1.200 Euro. Bei zwei Kindern bekämen Sie zum Beispiel insgesamt 24.000 Euro Baukindergeld ausgezahlt.</p>
    </div>
  </section>

  <!-- Kontakt page -->
  <section class="page contact-page">
    <svg class="contact-photo" width="378" height="184" viewBox="0 0 378 184">
      <g role="img" aria-label="Visualisierung eines modernen weißen Hauses mit Terrasse, Lounge-Möbeln und Garten">
        <rect width="378" height="184" fill="#c9d4cc"/>
      </g>
    </svg>
    <p class="contact-lead">Kontaktieren Sie uns gerne und<br>lassen Sie sich von uns beraten!</p>
    <div class="contact-lines">
      Lindenweg 7<br>DE-76530 Baden-Baden
      <div class="gap"></div>
      Mail: info@vorlind-bau.de<br>Tel: (+49) 0 7221 55 30 20<br>Fax: (+49) 0 7221 55 30 29
    </div>
    <div class="contact-web">www.vorlind-bau.de</div>
  </section>
</div>

<div class="stage">
</div>

<!-- Back cover -->
<section class="page back-page">
  <svg class="contact-photo" width="331" height="163" viewBox="0 0 331 163">
    <g role="img" aria-label="Visualisierung eines modernen weißen Hauses mit Terrasse, Lounge-Möbeln und Garten">
      <rect width="331" height="163" fill="#c9d4cc"/>
    </g>
  </svg>
  <p class="contact-lead">Kontaktieren Sie uns gerne und<br>lassen Sie sich von uns beraten!</p>
  <div class="contact-lines">
    Lindenweg 7<br>DE-76530 Baden-Baden
    <div class="gap"></div>
    Mail: info@vorlind-bau.de<br>Tel: (+49) 0 7221 55 30 20<br>Fax: (+49) 0 7221 55 30 29
  </div>
  <div class="contact-web">www.vorlind-bau.de</div>
</section>

<!-- Front cover -->
<section class="page cover-page">
  <div class="cover-brand">Vorlind Bauunternehmung</div>
  <svg class="cover-photo" width="332" height="254" viewBox="0 0 332 254">
    <g role="img" aria-label="Moderner weißer Neubau mit Holzfassade, Flachdach und gepflastertem Vorplatz">
      <polygon points="55,0 332,0 332,170 295,210 295,254 0,254 0,65" fill="#a9b6bf"/>
    </g>
  </svg>
  <p class="cover-claim">Fest-gefügt – Rundum aus einem Guss –<br>Vorlind Bauunternehmung aus Baden-Baden!</p>
</section>

</body>
</html>
```